Redesign Of Current Landing Page

I need to redesign this landing page https://www.brightlanepromo.biz/?page=landing&landing=23 (Please do not opt in because when you do it will show you the home page. Please clear your cookies before going to this url above to view the 1 page landing page.)

Please use my updated website as a reference for colors and logo.
http://sitecradlewerk.com/dh/bpq/index.html

I would like the call to action to be a button that opens into a lead form...

Button would be "Download Samples"

Target Market(s)

small business owners

Industry/Entity Type

Marketing

Number of Pages Required

1 page

Colors

Designer to choose colors to be used in the design.

Requirements
Must have
• must be full responsive on all devices
Nice to have
• must have a legitimate professional apeal to it
Should not have
• open

```html
<!DOCTYPE html>
<html lang="en">
<head>
<meta charset="utf-8">
<title>Bright Lane Promo Group – Landing</title>
<link rel="stylesheet" href="https://fonts.googleapis.com/css2?family=Mulish:wght@400;600;700&family=Open+Sans:ital,wght@0,400;0,600;1,400&display=swap">
<style>
:root{
  --blue:#0d63b8;
  --blue-deep:#0a4f9a;
  --orange:#f7a21b;
  --orange-deep:#ee8f0c;
  --ink:#222;
  --muted:#777;
  --rule:#ccc;
  --white:#fff;
  --dark:#2a2521;
}
*{margin:0;padding:0;box-sizing:border-box}
html,body{width:1200px;height:3136px;overflow:hidden}
body{font-family:"Open Sans",sans-serif;color:var(--ink);background:var(--white);position:relative}
.heading{font-family:"Mulish",sans-serif;font-weight:600;text-transform:uppercase;text-align:center;letter-spacing:.5px}
.rule{display:block;margin:14px auto 0;width:210px;height:2px;background:var(--rule);position:relative}
.rule::after{content:"";position:absolute;left:50%;top:-1px;width:54px;height:4px;margin-left:-27px;background:var(--blue)}
.btn{display:inline-block;font-family:"Mulish",sans-serif;font-weight:700;text-transform:uppercase;font-size:15px;color:var(--white);text-align:center}
.btn-orange{background:linear-gradient(var(--orange),var(--orange-deep));border-radius:3px;padding:14px 32px}

/* header */
.site-header{position:absolute;top:0;left:0;width:1200px;height:96px;display:flex;align-items:center}
.brand{position:absolute;left:120px;top:26px;display:flex;align-items:center;gap:10px}
.brand-mark{width:40px;height:40px;border-radius:50%;background:var(--blue)}
.brand-name{font-family:"Mulish",sans-serif;font-weight:700;font-size:32px;color:#1d2a44}
.main-nav{position:absolute;right:122px;top:36px;display:flex;gap:24px;font-family:"Mulish",sans-serif;font-size:17px;text-transform:uppercase;color:#333}
.main-nav .active{color:var(--blue)}

/* hero */
.hero{position:absolute;top:96px;left:0;width:1200px;height:580px;background:linear-gradient(180deg,#6c95b8 0%,#9fb8c8 30%,#7d5a3e 55%,#2a86b3 75%,#1f6c98 100%);text-align:center;color:var(--white)}
.hero-title{margin-top:214px;font-family:"Mulish",sans-serif;font-weight:700;font-size:39px;text-transform:uppercase}
.hero-sub{font-family:"Mulish",sans-serif;font-weight:700;font-size:24px;text-transform:uppercase;margin-top:6px}
.btn-outline{margin-top:26px;border:2px solid var(--white);padding:12px 36px;font-size:17px;font-weight:600}
.dots{position:absolute;top:540px;left:0;width:100%;display:flex;justify-content:center;gap:8px}
.dots span{width:13px;height:13px;border-radius:50%;background:var(--white)}
.dots span:first-child{background:transparent;border:2px solid var(--white)}

/* imagine */
.imagine{position:absolute;top:676px;left:0;width:1200px;height:446px;text-align:center}
.imagine .heading{margin-top:62px;font-size:34px;color:var(--blue)}
.imagine p{width:880px;margin:0 auto;font-size:14.5px;line-height:26px;color:var(--muted)}
.imagine p:first-of-type{margin-top:34px}
.imagine p+p{margin-top:14px}
.imagine .btn{margin-top:38px}

/* benefits */
.benefits{position:absolute;top:1122px;left:0;width:1200px;height:508px;background:radial-gradient(ellipse at 50% 40%,#5a4f47,var(--dark) 75%);color:var(--white)}
.benefits .heading{margin-top:60px;font-size:25px}
.benefits .rule{background:#777}
.benefits .rule::after{display:none}
.benefit-grid{position:absolute;top:160px;left:120px;display:grid;grid-template-columns:repeat(3,328px);row-gap:68px}
.benefit{display:flex;gap:20px}
.benefit-icon{width:88px;height:88px;flex:none;border-radius:50%;background:var(--blue);display:flex;align-items:center;justify-content:center}
.benefit h3{font-family:"Mulish",sans-serif;font-weight:600;font-size:17px;line-height:21px;margin-top:6px;width:220px}
.benefit p{font-size:10.5px;line-height:15px;color:#cfc8c2;margin-top:8px;width:200px}

/* how */
.how{position:absolute;top:1630px;left:0;width:1200px;height:505px}
.how .heading{margin-top:62px;font-size:28px;color:#111}
.how-photo{position:absolute;left:118px;top:144px;width:415px;height:272px;background:linear-gradient(180deg,#3f86cf 0%,#9cc6ea 35%,#6aa34a 60%,#2f9fc6 85%,#1a6fa5 100%)}
.how-copy{position:absolute;left:562px;top:142px;width:520px;font-size:14px;line-height:24.5px;color:var(--muted)}
.how-copy p+p{margin-top:12px}
.btn-blue{margin-top:18px;background:linear-gradient(var(--blue),var(--blue-deep));border-radius:3px;padding:13px 28px;font-size:13.5px}

/* testimonials */
.testimonials{position:absolute;top:2135px;left:0;width:1200px;height:455px;background:linear-gradient(180deg,#e6eef3,#f3f4f1 60%,#e9eae6)}
.testimonials .heading{margin-top:46px;font-size:26px;color:#111}
.quote-badge{position:absolute;left:572px;top:112px;width:58px;height:58px;border-radius:50%;background:var(--blue);display:flex;align-items:center;justify-content:center;z-index:2}
.quote-card{position:absolute;left:284px;top:145px;width:642px;height:216px;background:var(--white);box-shadow:0 2px 8px rgba(0,0,0,.18);padding:46px 40px 0;font-style:italic;font-size:12.5px;line-height:22px;text-align:center;color:#555}
.quote-name{position:absolute;top:378px;width:100%;text-align:center;font-family:"Mulish",sans-serif;font-weight:700;font-size:16px;color:#555}
.quote-place{position:absolute;top:403px;width:100%;text-align:center;font-size:11.5px;color:#777;text-transform:uppercase}

/* download */
.download{position:absolute;top:2590px;left:0;width:1200px;height:350px;background:linear-gradient(160deg,#0b4ea8,#1a76d2 55%,#0d56b0);text-align:center;color:var(--white)}
.download .heading{margin-top:84px;font-size:27px;font-weight:400}
.download .rule{background:rgba(255,255,255,.5);width:130px}
.download .rule::after{background:var(--white);width:40px;margin-left:-20px}
.download p{width:720px;margin:22px auto 0;font-size:16px;line-height:26px}
.download .btn{margin-top:22px;font-size:16px;font-weight:600}

/* footer */
.site-footer{position:absolute;top:2940px;left:0;width:1200px;height:196px;text-align:center}
.footer-nav{margin-top:48px;display:flex;justify-content:center;gap:24px;font-family:"Mulish",sans-serif;font-size:16px;text-transform:uppercase;color:#333}
.legal{margin-top:14px;font-size:14.5px;color:#888;font-weight:600}
.social{margin-top:16px;display:flex;justify-content:center;gap:6px}
.social span{width:30px;height:30px;border-radius:50%;border:2px solid var(--blue)}
</style>
</head>
<body>

<header class="site-header">
  <div class="brand"><span class="brand-mark"></span><span class="brand-name">BLPG</span></div>
  <nav class="main-nav">
    <span class="active">Home</span><span>About Us</span><span>Features</span><span>How It Works</span><span>Download Samples</span><span>Contact</span>
  </nav>
</header>

<section class="hero" role="img" aria-label="Luxury resort pool lined with wooden cabanas and palm trees under a blue sky">
  <h1 class="hero-title">Attract More Customers</h1>
  <p class="hero-sub">Who spend more money with your business more often!</p>
  <span class="btn btn-outline">Read More</span>
  <div class="dots"><span></span><span></span><span></span><span></span></div>
</section>

<section class="imagine">
  <h2 class="heading">Imagine</h2>
  <span class="rule"></span>
  <p>being able to create exciting give away promotions that will boost your sales without ever having to worry about cost.</p>
  <p>Bright Lane Promo Group, Inc. provides high-perceived value promotional incentives to businesses that want to advertise an exciting Give Away that will instantly attract more customers from your existing advertising efforts.</p>
  <p>Your business can give away incentive certificates that are redeemable for luxury hotel &amp; resort stays with airfare included, cruises, cash for gas, groceries, dining and even electronic goods.</p>
  <span class="btn btn-orange">Read More</span>
</section>

<section class="benefits">
  <h2 class="heading">Why offer incentives to customers?</h2>
  <span class="rule"></span>
  <div class="benefit-grid">
    <div class="benefit">
      <div class="benefit-icon"><svg width="40" height="40" viewBox="0 0 40 40" fill="none" stroke="#fff" stroke-width="3"><path d="M4 36h32M6 30l10-10 7 6 12-14"/><path d="M28 12h7v7"/></svg></div>
      <div><h3>Increase Responses From Your Existing Ads</h3><p>More replies from the ads you already pay for each month</p></div>
    </div>
    <div class="benefit">
      <div class="benefit-icon"><svg width="40" height="40" viewBox="0 0 40 40" fill="none" stroke="#fff" stroke-width="2.5"><path d="M20 4l4.5 10 10.5 1-8 7 2.5 10.5L20 27l-9.5 5.5L13 22l-8-7 10.5-1z"/></svg></div>
      <div><h3>Build Brand Awareness and Trust</h3><p>Give people a reason to remember your name and come back</p></div>
    </div>
    <div class="benefit">
      <div class="benefit-icon"><svg width="40" height="40" viewBox="0 0 40 40" fill="none" stroke="#fff" stroke-width="2.5"><path d="M34 6c-9 0-16 6-20 14l6 6c8-4 14-11 14-20z"/><circle cx="25" cy="15" r="2.5"/><path d="M14 20l-7 1-3 5 7 1M20 26l-1 7 5 3 1-7"/></svg></div>
      <div><h3>Boost Repeat and Referral Business</h3><p>Rewards that bring buyers back and get them telling friends</p></div>
    </div>
    <div class="benefit">
      <div class="benefit-icon"><svg width="40" height="40" viewBox="0 0 40 40" fill="none" stroke="#fff" stroke-width="3" stroke-linecap="round"><path d="M24 6a8 8 0 0 0 9 10L16 33a3.5 3.5 0 0 1-5-5L28 11a8 8 0 0 0-4-5z"/></svg></div>
      <div><h3>1 Sales Closing Tool - Gift w/ Purchase</h3><p>A free gift that turns a maybe into a signed sale today</p></div>
    </div>
    <div class="benefit">
      <div class="benefit-icon"><svg width="44" height="40" viewBox="0 0 44 40" fill="#fff"><circle cx="22" cy="12" r="6"/><path d="M12 32c0-7 4-11 10-11s10 4 10 11z"/><circle cx="9" cy="16" r="4.5"/><circle cx="35" cy="16" r="4.5"/><path d="M1 32c0-5 3-9 8-9 2 0 3 .5 4 1-2 2-3 5-3 8zM43 32c0-5-3-9-8-9-2 0-3 .5-4 1 2 2 3 5 3 8z"/></svg></div>
      <div><h3>Insure The Sale Over Your Competition</h3><p>Stand out so shoppers pick you over the shop next door</p></div>
    </div>
    <div class="benefit">
      <div class="benefit-icon"><svg width="40" height="40" viewBox="0 0 40 40" fill="none" stroke="#fff" stroke-width="2.5"><ellipse cx="20" cy="9" rx="12" ry="4"/><path d="M8 9v6c0 2 5 4 12 4s12-2 12-4V9M8 15v6c0 2 5 4 12 4s12-2 12-4v-6M8 21v6c0 2 5 4 12 4s12-2 12-4v-6"/></svg></div>
      <div><h3>Improve Retention Rates</h3><p>Keep loyal customers longer with perks they truly value</p></div>
    </div>
  </div>
</section>

<section class="how">
  <h2 class="heading">How can we do it?</h2>
  <span class="rule"></span>
  <div class="how-photo" role="img" aria-label="Tropical resort pool with white umbrellas, lounge chairs and palm trees"></div>
  <div class="how-copy">
    <p>We help fill empty rooms for thousands of hotels and resorts in hundreds of destinations around the world as well as the major cruise lines. Hotels and resorts are rarely full so when we place someone in their empty rooms, they end up making it up when travelers spend money on room service, spa services, eat at their in-house restaurants, casino and take advantage of other amenities that drive revenue.</p>
    <p>We also help over 18,000 restaurants, electronic manufacturers, the major gas companies and top grocery chains in the U.S and Canada increase brand awareness as well as increase customer loyalty.</p>
    <span class="btn btn-blue">Read More</span>
  </div>
</section>

<section class="testimonials" role="img" aria-label="Soft, faded view of a white terrace with lounge chairs by the sea">
  <h2 class="heading">Testimonials</h2>
  <span class="rule"></span>
  <div class="quote-badge"><svg width="22" height="18" viewBox="0 0 22 18" fill="#fff"><path d="M0 18V10C0 4 3 1 8 0l1 2C6 3 5 5 5 8h4v10zM13 18V10c0-6 3-9 8-10l1 2c-3 1-4 3-4 6h4v10z"/></svg></div>
  <blockquote class="quote-card">I began using your incentives two years ago to boost lead generation efforts. I have experienced a 63% increase in lead captures. And, even more importantly, my sales have increased as well. The ability to offer unlimited certificates and not having to pay for each certificate I give away is perhaps the best feature of the program, but having the flexibility to email or print certificates for my customers is also wonderful. I even use your html banners to automate my promotions right on my website!</blockquote>
  <div class="quote-name">DALE R.</div>
  <div class="quote-place">Fairview, TN</div>
</section>

<section class="download" role="img" aria-label="Blue-tinted photo of hands typing on a laptop keyboard">
  <h2 class="heading">Want to our download samples</h2>
  <span class="rule"></span>
  <p>sociosqu ad litora torquent per conubia nostra per inceptos hymenaeos Proin nulla arcu nonummy luctus dictum eget fermentum et lorem</p>
  <span class="btn btn-orange">Download Samples</span>
</section>

<footer class="site-footer">
  <nav class="footer-nav"><span>Home</span><span>About Us</span><span>Features</span><span>How It Works</span><span>Download Samples</span><span>Contact</span></nav>
  <p class="legal">© 2017 Company Name &nbsp;All right reserved &nbsp;Term of Use</p>
  <div class="social"><span></span><span></span><span></span><span></span></div>
</footer>

</body>
</html>
```